Stonebrace Business Card Design

The Stonebrace Co is an aggregate (crushing) equipment dealer serving Western Canadian provinces. Stonebrace is a distributor of aggregate equipment for different manufacturers.

We are looking to change and update the existing business card which has been used since the existence of the company. A copy of existing card has been attached for reference. The Stonebrace Co logo we want to remain the same and we want the green color to remain the same.

We are wanting something new with a different look. A refreshing card to show a new modern and updated look. No longer wanting to have the manufacturers on the back of the card but something more like our logo on the back of the card with a statement like "Crushing Solutions"

ideas could be:
- card can be different colors on front and back
- front or reverse of the card could possibly be the green color with the logo in black

Target Market(s)

Owners of Aggregate/Crushing companies

Contact Information for Business Card

see above

Requirements
Must have
• - logo to remain same along with same font within logo
• - green color to remain same
Nice to have
• as noted above under project description
Should not have

```html
<!DOCTYPE html>
<html lang="en">
<head>
<meta charset="utf-8">
<title>The Stonebrace Co – Business Card</title>
<link rel="stylesheet" href="https://fonts.googleapis.com/css2?family=Roboto:wght@400;700&family=Roboto+Condensed:wght@700&display=swap">
<style>
  :root {
    --backdrop: #5b4a3b;
    --card-dark: #231f20;
    --brand-green: #8a8a06;
    --ink-white: #ffffff;
    --ink-dark: #231f20;
  }
  * { margin: 0; padding: 0; box-sizing: border-box; }
  html, body { width: 1200px; height: 960px; overflow: hidden; }
  body {
    background: var(--backdrop);
    font-family: "Roboto", Arial, sans-serif;
    position: relative;
  }
  .card {
    position: absolute;
    width: 600px;
    height: 343px;
    border-radius: 18px;
    overflow: hidden;
  }
  .card--front { left: 314px; top: 113px; background: var(--card-dark); }
  .card--back { left: 311px; top: 472px; background: var(--brand-green); }

  .front-decoration {
    position: absolute;
    right: 0; top: 0;
    width: 325px; height: 100%;
    background: linear-gradient(100deg, var(--card-dark) 0%, #5a5a12 45%, var(--brand-green) 100%);
  }

  .contact-name {
    position: absolute; left: 43px; top: 42px;
    font-family: "Roboto Condensed", "Arial Narrow", sans-serif;
    font-weight: 700; font-size: 22px;
    color: var(--brand-green);
  }
  .contact-title {
    position: absolute; left: 44px; top: 68px;
    font-size: 15px; color: var(--ink-white);
  }
  .contact-address {
    position: absolute; left: 43px; top: 115px;
    font-size: 14.5px; line-height: 18px; color: var(--ink-white);
  }
  .contact-list {
    position: absolute; left: 43px; top: 165px;
    list-style: none;
  }
  .contact-list li {
    display: flex; align-items: center;
    height: 19.5px;
    font-size: 14.5px; color: var(--ink-white);
  }
  .contact-list svg { width: 14px; height: 14px; margin-right: 9px; fill: var(--brand-green); }
  .company-name {
    font-weight: 700; letter-spacing: 0.2px;
  }
  .card--front .company-name {
    position: absolute; left: 43px; top: 284px;
    font-size: 19px; color: var(--ink-white);
  }

  .back-lockup {
    position: absolute; left: 88px; top: 143px;
    display: flex; align-items: center; gap: 28px;
  }
  .back-lockup .brand-dot {
    width: 56px; height: 56px; border-radius: 50%;
    background: var(--ink-dark);
  }
  .card--back .company-name { font-size: 22px; color: var(--ink-dark); }
  .tagline {
    position: absolute; left: 0; right: 0; top: 292px;
    text-align: center;
    font-weight: 700; font-size: 14.5px; color: var(--ink-dark);
  }
</style>
</head>
<body>
  <section class="card card--front">
    <div class="front-decoration" role="img" aria-label="Decorative brand pattern area in olive green on charcoal"></div>
    <h1 class="contact-name">DALE MORWICK</h1>
    <p class="contact-title">CEO/FOUNDER</p>
    <p class="contact-address">2218- 71B Avenue<br>Nisku, Alberta T9E 3K1</p>
    <ul class="contact-list">
      <li><svg viewBox="0 0 16 16" aria-hidden="true"><path d="M3.6 1.2l2.2 2.6-1.2 1.8c.9 2 2.6 3.8 4.8 4.8l1.8-1.2 2.6 2.2-1.3 2.4C7.4 13.4 2.6 8.6 1.2 3.4z"/></svg>780.555.0147</li>
      <li><svg viewBox="0 0 16 16" aria-hidden="true"><path d="M4.5 0h7A1.5 1.5 0 0113 1.5v13a1.5 1.5 0 01-1.5 1.5h-7A1.5 1.5 0 013 14.5v-13A1.5 1.5 0 014.5 0zM5 2v10h6V2zm3 11a1 1 0 100 2 1 1 0 000-2z"/></svg>780.555.0182</li>
      <li><svg viewBox="0 0 16 16" aria-hidden="true"><path d="M4 1h8v4H4zM1 6h14v6h-2v3H3v-3H1zm4 4v3h6v-3z"/></svg>780.555.0139</li>
      <li><svg viewBox="0 0 16 16" aria-hidden="true"><path d="M1 3h14v10H1zm1.5 1.2L8 8.6l5.5-4.4z"/></svg>dale@stonebr.com</li>
      <li><svg viewBox="0 0 16 16" aria-hidden="true"><path d="M8 1a7 7 0 110 14A7 7 0 018 1zm-2 3.5L4 6l1.5 2L5 11l2 1.5 1-2.5 2-1-1-2.5 2-1L9 3z"/></svg>www.stonebrace.ca</li>
    </ul>
    <p class="company-name">THE STONEBRACE CO.</p>
  </section>

  <section class="card card--back">
    <div class="back-lockup">
      <span class="brand-dot" aria-hidden="true"></span>
      <p class="company-name">THE STONEBRACE CO.</p>
    </div>
    <p class="tagline">Crushing Solutions</p>
  </section>
</body>
</html>
```